Brochure for a website accessibility report

This brochure is related to a report that www.qelvantrix.org sell. The report shows the results of an automated audit of a websites accessibility. It shows details of issues found with screen shots, examples of code and provides remediation advice.

The brochure will be a pdf 8.5 inches by 11 inches. It can be anywhere from 6 to 10 pages.

The FlintVue™ name itself should be “Bree Serif” font. The fonts, styles, colors and sizes are up to you.

The images used and logo of the Office of Digital Reachworks and K7P logo are upload

We highlighted in blue page extracts from the report we sell. Do not use the blue highlight, it is merely there to show you where the specific examples of the report we sell are vs the other content in the report. The areas in blue which show the content from the actual report should be shown as an extract of the actual page of the report. You have flexibility to change the layout and the way the content look.

The red square callouts over the blue content are callouts that describe the specific page extracts. We used it as a red callout only so that you would be able to see it. You should change the specific location, look and feel of the callout to be appropriate

Target Market(s)

Marketing and Technical people

Industry/Entity Type

Information Technology

Font styles to use
Sans Serif

Colors

Designer to choose colors to be used in the design.

Requirements
Should not have
• wheelchairs, images of blind people

```html
<!DOCTYPE html>
<html lang="en">
<head>
<meta charset="utf-8">
<title>FlintVue™ Report Brochure – Office of Digital Reachworks</title>
<link rel="stylesheet" href="https://fonts.googleapis.com/css2?family=Bree+Serif&family=Lato:wght@400;700&family=Montserrat:wght@500;700&display=swap">
<style>
:root{
  --backdrop:#a7a8ad;
  --paper:#ffffff;
  --green:#2fb574;
  --green-light:#52c78c;
  --green-dark:#23975f;
  --band:#4a4a4a;
  --ink:#4a4d52;
  --ink-soft:#8a8d92;
  --blue:#1a56a8;
  --night:#17202f;
  --night-2:#2c3a52;
  --copper:#8a5a34;
}
*{margin:0;padding:0;box-sizing:border-box}
html,body{width:794px;height:1200px;overflow:hidden}
body{background:var(--backdrop);font-family:"Lato",Arial,sans-serif;color:var(--ink);position:relative}

.spread-slot{position:absolute;overflow:visible}
.spread{position:absolute;top:0;left:0;width:680px;height:440px;display:flex;transform-origin:0 0;box-shadow:0 6px 18px rgba(0,0,0,.28)}
.page{position:relative;width:340px;height:440px;overflow:hidden;background:var(--paper)}
.page--left{box-shadow:inset -14px 0 16px -14px rgba(0,0,0,.25)}

.slot-cover{left:97px;top:18px;width:600px;height:388px}
.slot-cover .spread{transform:scale(.8824)}
.slot-contents{left:18px;top:432px;width:370px;height:240px}
.slot-section-small{left:406px;top:432px;width:370px;height:240px}
.slot-contents .spread,.slot-section-small .spread{transform:scale(.5441)}
.slot-section{left:57px;top:700px;width:680px;height:440px}

/* cover */
.back-band{position:absolute;left:95px;top:200px;width:245px;height:88px;background:var(--band)}
.contact{position:absolute;left:40px;top:352px;font-size:5.6px;line-height:8px;color:var(--ink-soft)}
.contact__title{font-family:"Montserrat",sans-serif;font-weight:500;color:var(--green);font-size:10px;letter-spacing:3px;margin-bottom:4px}
.contact p+p{margin-top:4px}
.back-url{position:absolute;right:30px;top:388px;font-size:6px;color:var(--green)}
.page--cover{background:linear-gradient(160deg,var(--green-light) 0%,var(--green) 45%,var(--green-dark) 100%);color:#fff}
.cover-name{position:absolute;left:52px;top:184px;font-family:"Lato",sans-serif;font-weight:700;font-size:11px;letter-spacing:1.5px;text-transform:uppercase;color:#fff}
.cover-title{position:absolute;left:52px;top:208px;font-family:"Bree Serif",serif;font-size:31px;letter-spacing:4px}
.cover-sub{position:absolute;left:53px;top:248px;font-family:"Lato",sans-serif;font-weight:700;font-size:5.6px;letter-spacing:1.6px;text-transform:uppercase}

/* contents */
.contents-title{position:absolute;right:30px;top:38px;font-family:"Montserrat",sans-serif;font-weight:700;font-size:12px;letter-spacing:3px;color:var(--green)}
.toc{position:absolute;left:30px;top:70px;width:290px;display:grid;grid-template-columns:1fr 1fr;gap:12px 18px}
.toc__item{font-size:5.4px;line-height:7px;color:var(--ink-soft)}
.toc__num{font-family:"Montserrat",sans-serif;font-weight:700;font-size:10px;color:var(--green);margin-right:4px}
.toc__name{font-family:"Montserrat",sans-serif;font-size:6px;color:var(--green-dark)}
.map{position:absolute;left:28px;top:200px;width:290px;height:140px;background:radial-gradient(ellipse at 50% 50%,#cfd1d5 0%,#e4e5e8 70%,#fff 100%)}
.page-name{position:absolute;left:28px;top:372px;font-family:"Lato",sans-serif;font-weight:700;font-size:6.5px;letter-spacing:.8px;color:var(--green);text-transform:uppercase}
.page--green{background:linear-gradient(170deg,var(--green-light),var(--green) 60%,var(--green-dark));color:#fff}
.green-copy{position:absolute;left:30px;top:40px;width:270px;font-size:6px;line-height:8.4px}
.green-copy h2{font-family:"Bree Serif",serif;font-weight:400;font-size:15px;letter-spacing:1px;margin-bottom:10px}
.green-copy h3{font-size:7px;font-weight:700;margin:10px 0 5px}
.green-copy p+p{margin-top:6px}
.green-copy ul{list-style:none}
.green-copy li{padding-left:7px;position:relative;margin-bottom:4px}
.green-copy li::before{content:"";position:absolute;left:0;top:3px;width:3px;height:3px;background:#fff}

/* footers */
.folio{position:absolute;bottom:22px;display:flex;align-items:center;gap:6px;font-size:5.6px;font-variant:small-caps;letter-spacing:.5px}
.folio__rule{height:2px;width:150px}
.folio__bar{width:1px;height:12px}
.folio--left{left:30px;color:var(--blue)}
.folio--left .folio__rule,.folio--left .folio__bar{background:var(--blue)}
.folio--right{right:26px;color:#fff}
.folio--right .folio__rule,.folio--right .folio__bar{background:#fff}
.folio__num{font-family:"Montserrat",sans-serif;font-weight:700}

/* section */
.intro-copy{position:absolute;left:36px;top:44px;width:262px;font-size:6.2px;line-height:8.4px;color:var(--ink)}
.intro-copy p{margin-bottom:7px}
.intro-copy h4{color:var(--blue);font-size:6.4px;font-weight:700;margin-top:8px}
.partner{text-align:center;margin:10px 0 10px;font-family:"Lato",sans-serif;font-weight:700;font-size:7.5px;letter-spacing:.5px;color:var(--blue)}
.page--photo{background:linear-gradient(100deg,var(--copper) 0%,#4a3f40 22%,var(--night-2) 55%,var(--night) 100%)}
.photo-fill{position:absolute;inset:0;background:radial-gradient(circle at 75% 45%,rgba(190,140,100,.35),transparent 40%),radial-gradient(circle at 20% 80%,rgba(120,150,190,.25),transparent 45%)}
.section-panel{position:absolute;left:0;top:52px;width:282px;height:300px;background:rgba(12,16,24,.72);padding:26px 22px;color:#e9ecf1}
.section-panel h2{font-family:"Bree Serif",serif;font-weight:400;font-size:17px;letter-spacing:1.5px;color:#fff;margin-bottom:4px}
.section-panel__rule{width:60px;height:1px;background:#fff;margin-bottom:10px}
.section-panel p{font-size:5.8px;line-height:7.6px;margin-bottom:5px}
.summary{width:100%;border-collapse:collapse;font-size:4.3px;margin-top:10px;color:#fff}
.summary th{font-size:5px;font-weight:700;padding:2px 3px;border-bottom:1px solid rgba(255,255,255,.7)}
.summary td{padding:2.2px 3px;border-bottom:1px solid rgba(255,255,255,.35)}
.summary .principle{font-weight:700;text-align:center;border-right:1px solid rgba(255,255,255,.5);font-size:5px}
.summary .guide{border-right:1px solid rgba(255,255,255,.5);white-space:nowrap}
.summary .issues span{display:inline-block;min-width:15px;border-bottom:1px solid rgba(255,255,255,.8);margin-right:2px;text-align:center}
</style>
</head>
<body>

<div class="spread-slot slot-cover">
  <section class="spread">
    <div class="page page--left">
      <div class="back-band"></div>
      <div class="contact">
        <div class="contact__title">CONTACT</div>
        <p>Headquarters<br>Office of Digital Reachworks<br>2210 Harlow Avenue, Suite 400<br>Brenmoor Heights, CA 90211</p>
        <p>Phone: 555-014-0273<br>Email: contact@qelvantrix.org</p>
      </div>
      <div class="back-url">www.qelvantrix.org</div>
    </div>
    <div class="page page--cover">
      <div class="cover-name">Office of Digital Reachworks</div>
      <div class="cover-title">REPORT</div>
      <div class="cover-sub">Office of Digital Reachworks</div>
    </div>
  </section>
</div>

<div class="spread-slot slot-contents">
  <section class="spread">
    <div class="page page--left">
      <div class="contents-title">CONTENT</div>
      <div class="toc">
        <div class="toc__item"><span class="toc__num">01</span><span class="toc__name">FlintVue™</span><br>What the automated audit checks and how results are shown.</div>
        <div class="toc__item"><span class="toc__num">02</span><span class="toc__name">WCAG 2.1</span><br>Guidelines and checkpoints grouped by four principles.</div>
        <div class="toc__item"><span class="toc__num">03</span><span class="toc__name">Section 1</span><br>Summary chart of issues found for each guideline.</div>
        <div class="toc__item"><span class="toc__num">04</span><span class="toc__name">Section 2</span><br>Issue details with screenshots and code examples.</div>
        <div class="toc__item"><span class="toc__num">05</span><span class="toc__name">Remediation</span><br>Clear advice on fixing each failed checkpoint.</div>
        <div class="toc__item"><span class="toc__num">06</span><span class="toc__name">Notes</span><br>Next steps and support from our team.</div>
      </div>
      <div class="map" role="img" aria-label="Dotted grey world map"></div>
      <div class="page-name">Office of Digital Reachworks</div>
    </div>
    <div class="page page--green">
      <div class="green-copy">
        <h2>FLINTVUE™</h2>
        <p>FlintVue™ scans every page of your website and tests it against hundreds of rules based on WCAG 2.1 Level A/AA, then turns the results into a clear report.</p>
        <p>Each issue is explained with a screenshot, the failing code and a tested fix, so marketing and technical teams can act on it together.</p>
        <p>Reports can be run again after changes to track progress over time.</p>
        <h3>Quick Facts</h3>
        <ul>
          <li>Covers all 50 checkpoints of WCAG 2.1 Level A/AA.</li>
          <li>Shows the exact element and line of code that fails.</li>
          <li>Gives remediation advice written by accessibility experts.</li>
          <li>Sorts issues by principle so work can be planned.</li>
        </ul>
      </div>
      <div class="folio folio--right"><span class="folio__rule"></span><span>Our Mission and Vision</span><span class="folio__bar"></span><span class="folio__num">02</span></div>
    </div>
  </section>
</div>

<div class="spread-slot slot-section-small">
  <section class="spread">
    <div class="page page--left">
      <div class="intro-copy">
        <p>The Americans with Disabilities Act (ADA) is a comprehensive federal civil rights law prohibiting discrimination on the basis of disability, enforced by the Department of Justice (DOJ). Websites are considered places of public accommodations.</p>
        <div class="partner">Kestrel Web Panel (K7P)</div>
        <p>WCAG 2.1 Level A/AA consists of 13 guidelines with 50 checkpoints that are organized under four principles:</p>
        <h4>Principle 1: Perceivable</h4><p>Information must be presented in ways users can perceive.</p>
        <h4>Principle 2: Operable</h4><p>Interface components and navigation must be operable.</p>
        <h4>Principle 3: Understandable</h4><p>Information and operation must be understandable.</p>
      </div>
      <div class="folio folio--left"><span class="folio__num">03</span><span class="folio__bar"></span><span>Our Mission and Vision</span><span class="folio__rule"></span></div>
    </div>
    <div class="page page--photo">
      <div class="photo-fill" role="img" aria-label="Dark photo of glowing code on a screen with warm light"></div>
      <div class="section-panel">
        <h2>SECTION 1</h2>
        <div class="section-panel__rule"></div>
        <p>The first section of the report begins with a Summary Chart that breaks down WCAG 2.1 A/AA issues by principle.</p>
      </div>
      <div class="folio folio--right"><span class="folio__rule"></span><span>Our Mission and Vision</span><span class="folio__bar"></span><span class="folio__num">04</span></div>
    </div>
  </section>
</div>

<div class="spread-slot slot-section">
  <section class="spread">
    <div class="page page--left">
      <div class="intro-copy">
        <p>The Americans with Disabilities Act (ADA) is a comprehensive federal civil rights law prohibiting discrimination on the basis of disability, enforced by the Department of Justice (DOJ). The ADA prohibits discriminatory lack of access for individuals with disabilities to goods and services of public services and accommodations. Websites are considered places of public accommodations. The DOJ currently uses WCAG 2.1 Level A/AA as an accepted standard by which to measure a website's accessibility.</p>
        <div class="partner">Kestrel Web Panel (K7P)</div>
        <p>WCAG 2.1 Level A/AA consists of 13 guidelines with 50 checkpoints that are organized under four principles:</p>
        <h4>Principle 1: Perceivable</h4>
        <p>Information and user interface components must be presentable to users in ways they can perceive. This means that users must be able to comprehend the information being depicted: it can't be invisible to all their senses.</p>
        <h4>Principle 2: Operable</h4>
        <p>User interface components and navigation must be operable. The interface cannot require interaction that a user cannot perform.</p>
        <h4>Principle 3: Understandable</h4>
        <p>Information and the operation of a user interface must be understandable. Users must be able to understand the information as well as the operation of the user interface.</p>
        <h4>Principle 4: Robust</h4>
        <p>Content must be robust enough that it can be interpreted reliably by a wide variety of user agents, including assistive technologies. As technologies and user agents evolve, the content should remain accessible.</p>
        <p>Start your journey to a fully compliant website with FlintVue™. This detailed compliance and remediation report is generated based on scanning your website against hundreds of carefully-crafted rules, logging failures, and then generating feedback and recommendations on how to fix the problems based on our years of experience and proven best practices.</p>
      </div>
      <div class="folio folio--left"><span class="folio__num">03</span><span class="folio__bar"></span><span>Our Mission and Vision</span><span class="folio__rule"></span></div>
    </div>
    <div class="page page--photo">
      <div class="photo-fill" role="img" aria-label="Dark photo of glowing code on a screen with warm light"></div>
      <div class="section-panel">
        <h2>SECTION 1</h2>
        <div class="section-panel__rule"></div>
        <p>The first section of the report begins with a Summary Chart that breaks down WCAG 2.1 A/AA issues by principle.</p>
        <p>Example WCAG 2.1 A/AA Summary Chart: Checkpoints with failures detected are identified in the "Issues Discovered" column. The detail behind these failures is available in the next section.</p>
        <table class="summary">
          <thead><tr><th>Principle</th><th>Guideline</th><th>Issues Discovered</th></tr></thead>
          <tbody>
            <tr><td class="principle" rowspan="4">Perceivable</td><td class="guide">Guideline 1.1 Text Alternatives</td><td class="issues"><span>1.1.1</span></td></tr>
            <tr><td class="guide">Guideline 1.2 Time-based Media</td><td class="issues"><span>1.2.1</span><span>1.2.2</span><span>1.2.3</span><span>1.2.5</span></td></tr>
            <tr><td class="guide">Guideline 1.3 Adaptable</td><td class="issues"><span>1.3.1</span><span>1.3.4</span><span>1.3.5</span></td></tr>
            <tr><td class="guide">Guideline 1.4 Distinguishable</td><td class="issues"><span>1.4.1</span><span>1.4.3</span><span>1.4.4</span><span>1.4.11</span></td></tr>
            <tr><td class="principle" rowspan="3">Operable</td><td class="guide">Guideline 2.1 Keyboard Accessible</td><td class="issues"><span>2.1.1</span><span>2.1.2</span></td></tr>
            <tr><td class="guide">Guideline 2.2 Enough Time</td><td class="issues"><span>2.2.1</span><span>2.2.2</span></td></tr>
            <tr><td class="guide">Guideline 2.4 Navigable</td><td class="issues"><span>2.4.1</span><span>2.4.2</span><span>2.4.4</span><span>2.4.7</span></td></tr>
            <tr><td class="principle" rowspan="3">Understandable</td><td class="guide">Guideline 3.1 Readable</td><td class="issues"><span>3.1.1</span></td></tr>
            <tr><td class="guide">Guideline 3.2 Predictable</td><td class="issues"><span>3.2.1</span><span>3.2.2</span></td></tr>
            <tr><td class="guide">Guideline 3.3 Input Assistance</td><td class="issues"><span>3.3.2</span></td></tr>
            <tr><td class="principle">Robust</td><td class="guide">Guideline 4.1 Compatible</td><td class="issues"><span>4.1.1</span><span>4.1.2</span></td></tr>
          </tbody>
        </table>
      </div>
      <div class="folio folio--right"><span class="folio__rule"></span><span>Our Mission and Vision</span><span class="folio__bar"></span><span class="folio__num">04</span></div>
    </div>
  </section>
</div>

</body>
</html>
```